BRELWINCare.co.uk - Mental Health Clinic for Child and Adolescents

Updated 29/01/2018***
I am not sure you guys are getting the idea regards to the opening page / homescreen layout. Can you look at the new images I have uploaded (page 5, 6 and 7) These are some of the layouts I like but to incorporate my chosen images, with the BRELWIN commissioner, buttons and a sliding header bar.
I have written a strong brief, I am looking for a website, preferably wordpress as i know they are easy to maintain. I am looking for a one page site, with the top / opening page being full screen image with drop down categories. I have made a rough design, see full brief in word doc attached, there is some freedom to play around with the design aspect but it will need to relay all the content provided. I like a minimal feel. I have also attached some images that may be useful, but will need a new logo for BRELWIN Care. I have attached some logo idea's, it is up to you decide whether you want to use them.
I would prefer the homepage as full screen image, and the categories offered as a drop down or over the main image.
I have also attached linked to some competitors websites:
https://www.vorimant-health.co.uk/
http://www.qlbn.org.uk/
Industry/Entity Type
Clinic
Number of Pages Required
1 page
Font styles to use
Look and feel
Each slider illustrates characteristics of the customer's brand and the style your logo design should communicate.

```html
<!DOCTYPE html>
<html lang="en">
<head>
<meta charset="utf-8">
<title>BRELWIN Care – Contact and Team</title>
<link href="https://fonts.googleapis.com/css2?family=Kaushan+Script&family=Open+Sans:wght@400;600&family=Poppins:wght@400;500;600&display=swap" rel="stylesheet">
<style>
:root{
  --teal:#119a80;
  --plum:#1e0c16;
  --paper:#eeeeee;
  --white:#ffffff;
  --ink:#1b1b1b;
  --line:#e2e2e2;
  --photo-light-a:#d9d4cf;
  --photo-light-b:#6d7f8c;
  --photo-dark-a:#3a2a26;
  --photo-dark-b:#1f1714;
}
*{margin:0;padding:0;box-sizing:border-box}
html,body{width:1200px;height:1200px;overflow:hidden;background:var(--white)}
body{font-family:"Open Sans",sans-serif;color:var(--ink);position:relative}
.screen{position:absolute;left:0;width:1200px;height:594px;background:var(--paper);overflow:hidden}
.screen--contact{top:0}
.screen--team{top:603px}
.brand{position:absolute;left:0;top:0;width:165px;height:84px;background:var(--white);display:flex;align-items:center;justify-content:center}
.brand__name{display:flex;align-items:center;gap:7px;font-family:"Poppins",sans-serif;font-weight:600;font-size:22px;color:var(--teal);letter-spacing:.5px}
.brand__dot{width:12px;height:12px;border-radius:50%;background:var(--teal)}
.sidenav{position:absolute;left:0;top:84px;width:76px;height:510px;background:var(--white)}
.sidenav__item{position:absolute;left:11px;width:65px;height:74px;border-bottom:1px solid var(--line);display:flex;align-items:center;justify-content:center}
.sidenav__item svg{width:30px;height:30px;stroke:var(--ink);fill:none;stroke-width:1.4}
.sidenav__tab{position:absolute;left:11px;width:155px;height:74px;background:var(--teal);border-right:4px solid var(--plum);display:flex;align-items:center;gap:22px;padding-left:18px;color:var(--white);font-family:"Poppins",sans-serif;font-size:16px}
.sidenav__tab svg{width:28px;height:28px;stroke:var(--white);fill:none;stroke-width:1.4}
.page-title{position:absolute;left:255px;font-family:"Kaushan Script",cursive;font-size:58px;color:var(--ink);font-weight:400}
.contact-list{position:absolute;left:255px;top:158px;list-style:none}
.contact-list li{margin-bottom:11px}
.contact-list__label{display:flex;align-items:center;gap:8px;font-weight:600;font-size:15px}
.contact-list__label svg{width:15px;height:15px;stroke:var(--teal);fill:none;stroke-width:1.5}
.contact-list__value{padding-left:22px;margin-top:9px;font-size:14px;color:#333}
.footer-note{position:absolute;left:0;width:1214px;text-align:center;top:564px;font-family:"Poppins",sans-serif;font-size:11px;color:var(--ink)}
.hero-shape{position:absolute;left:820px;top:40px;width:380px;height:540px}
.swap-icon{position:absolute;left:190px;top:278px;width:46px;height:40px}
.team-cards{position:absolute;top:211px;left:255px;display:flex;gap:25px}
.team-card{position:relative;width:157px;height:219px;box-shadow:0 6px 14px rgba(0,0,0,.18);overflow:hidden;background:var(--teal)}
.team-card:nth-child(3){margin-left:3px}
.team-card__photo{position:absolute;inset:0;background:linear-gradient(180deg,#dfe3e6,#b9aea4)}
.team-card__band{position:absolute;left:0;right:0;bottom:0;height:100px;background:var(--teal);clip-path:polygon(0 23px,100% 0,100% 100%,0 100%)}
.team-card--featured .team-card__band{background:var(--plum)}
.team-card__name{position:absolute;left:0;right:0;top:151px;text-align:center;font-family:"Kaushan Script",cursive;font-size:19px;font-weight:400;color:var(--white)}
.team-card__role{position:absolute;left:0;right:0;top:183px;text-align:center;font-family:"Poppins",sans-serif;font-size:11px;color:var(--white)}
</style>
</head>
<body>

<section class="screen screen--contact">
  <div class="brand">
    <div class="brand__name"><span class="brand__dot"></span>BRELWIN</div>
  </div>
  <nav class="sidenav">
    <div class="sidenav__item" style="top:7px"><svg viewBox="0 0 30 30"><path d="M4 8h22M4 15h22M4 22h22"/></svg></div>
    <div class="sidenav__item" style="top:87px"><svg viewBox="0 0 30 30"><rect x="5" y="5" width="18" height="22"/><path d="M5 9h18M9 14h8M9 18h6M14 24l12-12 2 2-12 12h-2z"/></svg></div>
    <div class="sidenav__item" style="top:161px"><svg viewBox="0 0 30 30"><circle cx="15" cy="10" r="4"/><circle cx="8" cy="13" r="3"/><circle cx="22" cy="13" r="3"/><path d="M8 26v-5a7 7 0 0 1 14 0v5M3 26v-4a5 5 0 0 1 5-5M27 26v-4a5 5 0 0 0-5-5"/></svg></div>
    <div class="sidenav__item" style="top:235px"><svg viewBox="0 0 30 30"><path d="M5 22L20 7l3 3L8 25H5zM6 7l3-3 17 17-3 3z"/></svg></div>
    <div class="sidenav__tab" style="top:318px"><svg viewBox="0 0 30 30"><path d="M7 4l5 5-3 3a14 14 0 0 0 9 9l3-3 5 5-4 4C12 26 4 18 3 8z"/></svg>CONTACT</div>
    <div class="sidenav__item" style="top:403px"><svg viewBox="0 0 30 30"><rect x="3" y="5" width="24" height="20"/><path d="M3 11h24M3 18h24M7 8h10M7 14h14M7 21h8"/></svg></div>
  </nav>

  <h1 class="page-title" style="top:48px">Contact Us</h1>

  <ul class="contact-list">
    <li>
      <div class="contact-list__label"><svg viewBox="0 0 16 16"><path d="M4 1l3 3-2 2a8 8 0 0 0 5 5l2-2 3 3-2 2C7 14 2 9 2 3z"/></svg>Phone Number</div>
      <div class="contact-list__value">0203 555 0182</div>
    </li>
    <li>
      <div class="contact-list__label"><svg viewBox="0 0 16 16"><path d="M8 15s5-5 5-9a5 5 0 0 0-10 0c0 4 5 9 5 9z"/><circle cx="8" cy="6" r="2"/></svg>Address</div>
      <div class="contact-list__value">Ashgrove Suite 2B, 41-47 Mill Lane, London, E17 4PR</div>
    </li>
    <li>
      <div class="contact-list__label"><svg viewBox="0 0 16 16"><circle cx="8" cy="9" r="6"/><path d="M8 6v3h2M2 3l2-2M14 3l-2-2"/></svg>Opening Times</div>
      <div class="contact-list__value">9am – 5pm Mon-Fri</div>
    </li>
    <li>
      <div class="contact-list__label"><svg viewBox="0 0 16 16"><rect x="1" y="3" width="14" height="10"/><path d="M1 3l7 6 7-6"/></svg>Email</div>
      <div class="contact-list__value">enquiry@brelwincare.co.uk</div>
    </li>
  </ul>

  <svg class="hero-shape" viewBox="0 0 380 540">
    <defs>
      <linearGradient id="lightPhoto" x1="0" y1="0" x2="1" y2="1">
        <stop offset="0" stop-color="#d9d4cf"/>
        <stop offset="1" stop-color="#6d7f8c"/>
      </linearGradient>
    </defs>
    <path d="M32 103 Q18 112 24 132 L100 410 Q112 436 150 456 L380 540 L380 18 Z" fill="none" stroke="#119a80" stroke-width="6"/>
    <path role="img" aria-label="Photo of three smiling teenagers sitting together on a sofa" d="M46 110 Q32 118 38 138 L110 405 Q122 430 158 448 L380 528 L380 30 Z" fill="url(#lightPhoto)"/>
  </svg>

  <p class="footer-note">© 2018 All Rights Reserved.brelwin.com</p>
</section>

<section class="screen screen--team">
  <div class="brand">
    <div class="brand__name"><span class="brand__dot"></span>BRELWIN</div>
  </div>
  <nav class="sidenav">
    <div class="sidenav__item" style="top:7px"><svg viewBox="0 0 30 30"><path d="M4 8h22M4 15h22M4 22h22"/></svg></div>
    <div class="sidenav__item" style="top:87px"><svg viewBox="0 0 30 30"><rect x="5" y="5" width="18" height="22"/><path d="M5 9h18M9 14h8M9 18h6M14 24l12-12 2 2-12 12h-2z"/></svg></div>
    <div class="sidenav__tab" style="top:163px"><svg viewBox="0 0 30 30"><circle cx="15" cy="10" r="4"/><circle cx="8" cy="13" r="3"/><circle cx="22" cy="13" r="3"/><path d="M8 26v-5a7 7 0 0 1 14 0v5M3 26v-4a5 5 0 0 1 5-5M27 26v-4a5 5 0 0 0-5-5"/></svg><span style="padding-left:12px">TEAM</span></div>
    <div class="sidenav__item" style="top:241px"><svg viewBox="0 0 30 30"><path d="M5 22L20 7l3 3L8 25H5zM6 7l3-3 17 17-3 3z"/></svg></div>
    <div class="sidenav__item" style="top:322px"><svg viewBox="0 0 30 30"><path d="M7 4l5 5-3 3a14 14 0 0 0 9 9l3-3 5 5-4 4C12 26 4 18 3 8z"/></svg></div>
    <div class="sidenav__item" style="top:403px"><svg viewBox="0 0 30 30"><rect x="3" y="5" width="24" height="20"/><path d="M3 11h24M3 18h24M7 8h10M7 14h14M7 21h8"/></svg></div>
  </nav>

  <h1 class="page-title" style="top:94px">Our Team</h1>

  <svg class="hero-shape" viewBox="0 0 380 540">
    <defs>
      <linearGradient id="darkPhoto" x1="0" y1="0" x2="1" y2="1">
        <stop offset="0" stop-color="#3a2a26"/>
        <stop offset="1" stop-color="#1f1714"/>
      </linearGradient>
    </defs>
    <path d="M32 103 Q18 112 24 132 L100 410 Q112 436 150 456 L380 540 L380 18 Z" fill="none" stroke="#119a80" stroke-width="6"/>
    <path role="img" aria-label="Dimmed photo of a young person in conversation" d="M46 110 Q32 118 38 138 L110 405 Q122 430 158 448 L380 528 L380 30 Z" fill="url(#darkPhoto)"/>
  </svg>

  <svg class="swap-icon" viewBox="0 0 46 40" fill="none" stroke-width="1.8">
    <path d="M44 14a8 8 0 0 0-8-8H22M27 1l-5 5 5 5" stroke="#119a80"/>
    <path d="M2 26a8 8 0 0 0 8 8h14M19 29l5 5-5 5" stroke="#1b1b1b"/>
    <path d="M2 26a8 8 0 0 1 8-8" stroke="#1b1b1b"/>
  </svg>

  <div class="team-cards">
    <article class="team-card team-card--featured">
      <div class="team-card__photo" role="img" aria-label="Portrait of a clinician in a white blouse holding a tablet"></div>
      <div class="team-card__band"></div>
      <h2 class="team-card__name">Maren Doyle</h2>
      <p class="team-card__role">Halden Securities</p>
    </article>
    <article class="team-card">
      <div class="team-card__photo" role="img" aria-label="Portrait of a smiling man in a dark polo shirt" style="background:linear-gradient(180deg,#c9bfae,#6a6a70)"></div>
      <div class="team-card__band"></div>
      <h2 class="team-card__name">Tobin Hale</h2>
      <p class="team-card__role">Halden Securities</p>
    </article>
    <article class="team-card">
      <div class="team-card__photo" role="img" aria-label="Portrait of a smiling woman with long hair in a blue top" style="background:linear-gradient(180deg,#b8a894,#7c8ea6)"></div>
      <div class="team-card__band"></div>
      <h2 class="team-card__name">Maren Doyle</h2>
      <p class="team-card__role">Halden Securities</p>
    </article>
    <article class="team-card">
      <div class="team-card__photo" role="img" aria-label="Portrait of a smiling man in a white polo shirt" style="background:linear-gradient(180deg,#ffffff,#d8d2cc)"></div>
      <div class="team-card__band"></div>
      <h2 class="team-card__name">Callum Hale</h2>
      <p class="team-card__role">Halden Securities</p>
    </article>
  </div>

  <p class="footer-note" style="top:562px">© 2018 All Rights Reserved.brelwin.com</p>
</section>

</body>
</html>
```